KTWG application splash screen

We need a 1024x768 image for use as an application splash screen.
The image will be displayed full screen on an 10 inch industrial PC 1024x768 screen while our application is launching. The image should convey that the application is "Waiting for connection to Wi-Fi access point..." and include a graphic of the industrial PC connected to the access point via an Ethernet cable. A list of troubleshooting steps should be included at the bottom of the image. The troubleshooting steps should not be the main focus of the image and should be shown in a smaller font (but still readable at 1024x768 displayed on a 10 inch screen).
I will include a mock up of the general idea of what we are looking for as well as image files for the industrial PC, a screenshot of our application to show on the PC's screen and the AP.
For general look and feel and a sense of corporate branding please review our website https://marrowgatesoilworks.example/. The splash screen should reflect corporate branding.
Target Market(s)
Users of our application
Industry/Entity Type
Agriculture
Look and feel

```html
<!DOCTYPE html>
<html lang="en">
<head>
<meta charset="utf-8">
<title>KTWG – Waiting for Wi-Fi access point</title>
<link rel="stylesheet" href="https://fonts.googleapis.com/css2?family=Poppins:wght@400;500;700&display=swap">
<style>
  :root {
    --page-bg: #e8e8e8;
    --brand-green: #4f9f68;
    --ink: #3a3a3a;
    --ink-dark: #222222;
    --white: #ffffff;
    --device-tone: #2f3336;
    --cable-tone: #3f6d4e;
    --ap-tone: #e9ecea;
  }
  * { margin: 0; padding: 0; box-sizing: border-box; }
  html, body { width: 1200px; height: 1200px; overflow: hidden; background: var(--page-bg); }
  body { font-family: "Poppins", sans-serif; color: var(--ink); }

  .splash {
    position: absolute; left: 0; top: 150px;
    width: 1200px; height: 900px;
    background: var(--white); overflow: hidden;
  }
  .splash__band { position: absolute; inset: 0; }

  .splash__title {
    position: absolute; left: 0; right: 0; top: 36px;
    text-align: center; color: var(--white);
    font-weight: 400; font-size: 66px; line-height: 60px;
    letter-spacing: 0.5px; text-transform: uppercase;
  }

  .illustration {
    position: absolute; left: 176px; top: 154px;
    width: 854px; height: 302px; border-radius: 14px;
    background: linear-gradient(90deg, var(--device-tone) 0%, var(--device-tone) 30%, var(--cable-tone) 55%, var(--brand-green) 78%, var(--ap-tone) 100%);
  }

  .troubleshoot__label {
    position: absolute; left: 77px; top: 538px;
    width: 447px; height: 37px; border-radius: 19px;
    background: var(--ink); color: var(--white);
    font-weight: 700; font-size: 27px; line-height: 37px;
    padding-left: 35px; letter-spacing: 0.2px;
  }

  .steps { position: absolute; left: 0; top: 0; width: 1200px; height: 900px; }
  .step {
    position: absolute; font-weight: 500; font-size: 19.5px;
    line-height: 24px; color: var(--ink); white-space: nowrap;
  }
  .step--main { left: 102px; }
  .step--sub { left: 134px; }

  .brand {
    position: absolute; left: 898px; top: 732px;
    display: flex; align-items: center; gap: 14px;
  }
  .brand__dot { width: 56px; height: 56px; border-radius: 50%; background: var(--brand-green); }
  .brand__name { font-weight: 700; font-size: 64px; line-height: 64px; color: var(--ink-dark); letter-spacing: 1px; }
</style>
</head>
<body>
<main class="splash">
  <svg class="splash__band" width="1200" height="900" viewBox="0 0 1200 900" aria-hidden="true">
    <polygon points="0,0 1200,0 1200,569 0,472" fill="var(--brand-green)"/>
  </svg>

  <h1 class="splash__title">Waiting for connection to<br>Wi-Fi access point...</h1>

  <div class="illustration" role="img" aria-label="Industrial PC showing the seeding application, joined by a coiled Ethernet cable to an outdoor Wi-Fi access point"></div>

  <div class="troubleshoot__label">TROUBLESHOOTING STEPS:</div>

  <svg class="steps" width="1200" height="900" viewBox="0 0 1200 900" aria-hidden="true">
    <g stroke="var(--brand-green)" fill="none" stroke-width="2">
      <line x1="85" y1="591" x2="85" y2="825"/>
      <line x1="117" y1="660" x2="117" y2="838"/>
      <g stroke-width="2.2">
        <circle cx="85" cy="615" r="9"/><polyline points="80,615 84,619 95,605"/>
        <circle cx="85" cy="646" r="9"/><polyline points="80,646 84,650 95,636"/>
        <circle cx="117" cy="677" r="9"/><polyline points="112,677 116,681 127,667"/>
        <circle cx="117" cy="732" r="9"/><polyline points="112,732 116,736 127,722"/>
        <circle cx="117" cy="784" r="9"/><polyline points="112,784 116,788 127,774"/>
        <circle cx="117" cy="817" r="9"/><polyline points="112,817 116,821 127,807"/>
      </g>
    </g>
  </svg>

  <p class="step step--main" style="top:603px">This screen should only be visible for a short time on boot.</p>
  <p class="step step--main" style="top:634px">If this screen stays visible for more than a minute:</p>
  <p class="step step--sub" style="top:665px">Verify that the Wi-Fi Access Point (AP) powers up when this system does<br>(indicated by a green light on the side of the AP).</p>
  <p class="step step--sub" style="top:720px">Check the Ethernet cable between this system and the AP for damage<br>and replace it if necessary.</p>
  <p class="step step--sub" style="top:772px">Power-cycle this system and wait for it to reboot fully.</p>
  <p class="step step--sub" style="top:805px">If the issue persists, contact KTWG support for further assistance.</p>

  <div class="brand">
    <span class="brand__dot"></span>
    <span class="brand__name">KTWG</span>
  </div>
</main>
</body>
</html>
```